Premium Business Card for Wealth Creation

Please see attached business card for example.
Happy to look at options like Blue background with Yellow
Target Market(s)
People who want to buy investment property or create wealth
Industry/Entity Type
Investment
Contact Information for Business Card
Tel: 1800 314 579
Mobile: 0417 265 904
Address: Suite 3, 64 Carrow Lane Marlowe Vic 3942
Name: Martin Feldway
Title: CEO
Website: www.quolvane.com.au
Email: martin@quolvane.com.au
Font styles to use
Sans Serif
Colors
0255a3
fbed22
Requirements
Must have
- Look great

```html
<!DOCTYPE html>
<html lang="en">
<head>
<meta charset="utf-8">
<title>Quolvane Business Card</title>
<link rel="stylesheet" href="https://fonts.googleapis.com/css2?family=Open+Sans:wght@400;600;700;800&display=swap">
<style>
  :root {
    --brand-blue: #3461c1;
    --brand-yellow: #f5d330;
    --title-yellow: #e8c21e;
    --ink-blue: #3a5fb8;
    --card-white: #fbfbfb;
    --card-edge: #e2e2e2;
    --backdrop: #ecebe8;
  }
  * { box-sizing: border-box; margin: 0; padding: 0; }
  html, body {
    width: 1200px;
    height: 780px;
    overflow: hidden;
    background: var(--backdrop);
    font-family: "Open Sans", sans-serif;
  }
  .stage {
    width: 1200px;
    height: 780px;
    display: flex;
    align-items: center;
    justify-content: center;
    gap: 40px;
  }
  .card {
    width: 560px;
    height: 320px;
    background: linear-gradient(135deg, #ffffff 0%, var(--card-white) 60%, #f1f1f1 100%);
    border: 1px solid var(--card-edge);
    box-shadow: 0 6px 18px rgba(0,0,0,0.12);
    position: relative;
  }

  /* Front: identity left, details right */
  .card-front {
    display: flex;
    align-items: center;
  }
  .identity {
    width: 270px;
    display: flex;
    flex-direction: column;
    align-items: center;
    gap: 14px;
  }
  .brand-dot {
    width: 62px;
    height: 62px;
    border-radius: 50%;
    background: var(--brand-yellow);
  }
  .brand-name {
    font-weight: 800;
    color: var(--brand-blue);
    font-size: 30px;
    letter-spacing: 1px;
    white-space: nowrap;
  }
  .divider {
    width: 2px;
    height: 230px;
    background: linear-gradient(to bottom, rgba(52,97,193,0.25), var(--brand-blue) 40%, rgba(52,97,193,0.25));
  }
  .details {
    padding-left: 34px;
    color: var(--ink-blue);
  }
  .person-name {
    font-size: 22px;
    font-weight: 700;
    color: var(--brand-blue);
    line-height: 1.1;
  }
  .person-title {
    font-size: 14px;
    color: var(--title-yellow);
    margin-bottom: 16px;
  }
  .address {
    font-size: 13px;
    line-height: 1.45;
    margin-bottom: 8px;
  }
  .contact-list { list-style: none; }
  .contact-item {
    display: flex;
    align-items: center;
    gap: 8px;
    font-size: 13px;
    line-height: 1.55;
    white-space: nowrap;
  }
  .contact-icon {
    width: 15px;
    height: 15px;
    background: var(--brand-yellow);
    display: inline-flex;
    align-items: center;
    justify-content: center;
    flex: none;
  }

  /* Back: centred brand */
  .card-back {
    display: flex;
    align-items: center;
    justify-content: center;
    gap: 18px;
  }
  .card-back .brand-dot {
    width: 70px;
    height: 70px;
  }
  .card-back .brand-name {
    font-size: 48px;
  }
</style>
</head>
<body>
<main class="stage">
  <section class="card card-front" aria-label="Business card front">
    <div class="identity">
      <span class="brand-dot"></span>
      <span class="brand-name">QUOLVANE</span>
    </div>
    <div class="divider"></div>
    <div class="details">
      <p class="person-name">Martin Feldway</p>
      <p class="person-title">CEO</p>
      <p class="address">Suite 3, 64 Carrow Lane<br>Marlowe Vic 3942</p>
      <ul class="contact-list">
        <li class="contact-item">
          <span class="contact-icon"><svg width="10" height="10" viewBox="0 0 10 10"><path d="M2 1h2l1 2-1 1c.5 1 1 1.5 2 2l1-1 2 1v2c-4 0-7-3-7-7z" fill="#fff"/></svg></span>
          1800 314 579
        </li>
        <li class="contact-item">
          <span class="contact-icon"><svg width="10" height="10" viewBox="0 0 10 10"><rect x="3" y="0.5" width="4" height="9" rx="0.8" fill="#fff"/><rect x="3.8" y="1.6" width="2.4" height="5.5" fill="#f5d330"/></svg></span>
          0417 265 904
        </li>
        <li class="contact-item">
          <span class="contact-icon"><svg width="10" height="10" viewBox="0 0 10 10"><rect x="1" y="2.5" width="8" height="5.5" fill="#fff"/><path d="M1 2.5l4 3 4-3" fill="none" stroke="#f5d330" stroke-width="0.9"/></svg></span>
          martin@quolvane.com.au
        </li>
        <li class="contact-item">
          <span class="contact-icon"><svg width="10" height="10" viewBox="0 0 10 10"><circle cx="5" cy="5" r="3.8" fill="none" stroke="#fff" stroke-width="1"/><path d="M1.2 5h7.6M5 1.2c-2 2.4-2 5.2 0 7.6M5 1.2c2 2.4 2 5.2 0 7.6" fill="none" stroke="#fff" stroke-width="0.8"/></svg></span>
          www.quolvane.com.au
        </li>
      </ul>
    </div>
  </section>

  <section class="card card-back" aria-label="Business card back">
    <span class="brand-dot"></span>
    <span class="brand-name">QUOLVANE</span>
  </section>
</main>
</body>
</html>
```